Poloshirt Packaging

We need a very attractive packaging design for our poloshirts. We are wholesaler of the schoolwear market. See what we currently have. I dont want any specific sizing put on the packaging. One design for all poloshirts (2 sides).
our logo is attached aswell

Target Market(s)

Parents

Requirements
Must have
• Our logo
Should not have
• size or age

```html
<!DOCTYPE html>
<html lang="en">
<head>
<meta charset="utf-8">
<title>Brightway Poloshirt Packaging</title>
<link rel="stylesheet" href="https://fonts.googleapis.com/css2?family=Poppins:wght@500;600;700&family=Roboto:wght@400;500&display=swap">
<style>
  :root {
    --paper: #ffffff;
    --shadow: #9a9a9a;
    --edge: #3a3a3a;
    --coral: #f26b4f;
    --coral-deep: #e85a40;
    --tangerine: #f08b3d;
    --tangerine-deep: #e97a30;
    --navy: #1d2f5f;
    --red: #e0302a;
    --red-soft: #d9402e;
    --amber: #f5b81c;
    --flame: #e4482b;
  }
  * { margin: 0; padding: 0; box-sizing: border-box; }
  html, body { width: 1200px; height: 867px; overflow: hidden; background: var(--paper); }
  .canvas { position: relative; width: 1200px; height: 867px; background: var(--paper); }
  .panel {
    position: absolute; top: 20px; width: 578px; height: 817px; overflow: hidden;
    border: 1px solid var(--edge);
    box-shadow: 6px 6px 0 var(--shadow);
  }
  .panel--front { left: 18px; }
  .panel--back { left: 595px; }
  .panel svg.art { position: absolute; inset: 0; width: 100%; height: 100%; }
  .brand-name {
    position: absolute; font-family: "Poppins", sans-serif; font-weight: 600;
    color: var(--navy); letter-spacing: 0.5px; line-height: 1; white-space: nowrap;
  }
  .panel--front .brand-name { left: 48px; top: 545px; font-size: 68px; }
  .panel--back .brand-name { left: 0; right: 0; text-align: center; top: 258px; font-size: 60px; }
  .product-title {
    position: absolute; left: 50px; top: 622px; font-family: "Poppins", sans-serif;
    font-weight: 700; font-size: 34px; color: var(--red-soft); opacity: 0.75;
    letter-spacing: 1px; line-height: 1;
  }
  .feature-bar {
    position: absolute; left: 52px; top: 686px; background: var(--navy); color: var(--paper);
    font-family: "Roboto", sans-serif; font-size: 12.5px; padding: 3px 7px; white-space: nowrap;
  }
</style>
</head>
<body>
<main class="canvas">

  <section class="panel panel--front">
    <svg class="art" viewBox="0 0 578 817" preserveAspectRatio="none">
      <defs>
        <linearGradient id="frontWave" x1="0" y1="0" x2="1" y2="0">
          <stop offset="0" stop-color="var(--flame)"/>
          <stop offset="1" stop-color="var(--amber)"/>
        </linearGradient>
        <linearGradient id="frontPhoto" x1="0" y1="0" x2="0" y2="1">
          <stop offset="0" stop-color="var(--coral-deep)"/>
          <stop offset="1" stop-color="var(--coral)"/>
        </linearGradient>
      </defs>
      <rect width="578" height="817" fill="url(#frontPhoto)" role="img" aria-label="Photograph of a folded coral polo shirt in clear packaging, collar and button placket visible"/>
      <path d="M0 400 C120 380 210 300 310 235 C390 185 470 160 578 200 L578 262 C480 225 410 255 330 305 C230 370 120 470 0 492 Z" fill="url(#frontWave)"/>
      <path d="M400 817 C455 745 515 700 578 688 L578 817 Z" fill="var(--red)"/>
    </svg>
    <div class="brand-name">Brightway</div>
    <div class="product-title">POLOSHIRT</div>
    <div class="feature-bar">Superior weight fabric | Easy care - Low iron | Reactive dyed</div>
  </section>

  <section class="panel panel--back">
    <svg class="art" viewBox="0 0 578 817" preserveAspectRatio="none">
      <defs>
        <linearGradient id="backWave" x1="0" y1="0" x2="1" y2="0">
          <stop offset="0" stop-color="var(--amber)"/>
          <stop offset="1" stop-color="var(--flame)"/>
        </linearGradient>
        <linearGradient id="backPhoto" x1="0" y1="0" x2="0" y2="1">
          <stop offset="0" stop-color="var(--tangerine-deep)"/>
          <stop offset="1" stop-color="var(--tangerine)"/>
        </linearGradient>
      </defs>
      <rect width="578" height="817" fill="url(#backPhoto)" role="img" aria-label="Photograph of the back of a folded orange polo shirt in clear plastic packaging"/>
      <path d="M0 425 C100 470 200 370 330 372 C440 375 500 440 578 428 L578 578 C500 592 430 525 330 512 C220 500 110 590 0 510 Z" fill="url(#backWave)"/>
      <path d="M430 817 C480 750 530 712 578 705 L578 817 Z" fill="var(--red)"/>
    </svg>
    <div class="brand-name">Brightway</div>
  </section>

</main>
</body>
</html>
```